Calden L - Premium Business Cards

Background of Calden L
Calden Leafworks is a cigar mobile lounge where guests become family. A place of luxury, relaxation, and ambiance is the global popularity demand. Calden Leafworks strives to provide first-class service of quality and products. Our goal is to ensure that every guest is treated and serviced as a VIP.

Calden Leafworks was founded by Dennis Markow Jr in January 2020. After 15 years of cigar reviews and research Dennis decided it was time to launch his own cigar brand and boutique cigar company. With a wealth of knowledge and years of experience Calden Leafworks was born. With opulence for all cultures, Calden Leafworks offers hand rolled cigars with premium blend tobacco from sweet to bold imported from Costa Rica, Dominican Republic, and Nicaragua. Thank you for your business!

Objective:
Create a business card template to be used for all employees. Design should communicate premium and classy. And should use earth tone colors.

Design should include:
1. Client wants to incorporate the cigar leaf
2. Logo
3. Tagline: Savor every leaf
3. Content info:
Kevin Oldacre
Owner
555-017-4863
koldacre@caldenleaf.com
caldenleafworks.com

```html
<!DOCTYPE html>
<html lang="en">
<head>
<meta charset="utf-8">
<title>Calden Leafworks – Business Cards</title>
<link href="https://fonts.googleapis.com/css2?family=Montserrat:wght@600;700&family=Arimo:wght@400;700&display=swap" rel="stylesheet">
<style>
  :root {
    --backdrop: #d9d6d4;
    --card: #2b2728;
    --ink: #ffffff;
    --ink-soft: #e6e3e1;
    --rule: #bdb8b6;
    --smoke-a: #3a3536;
    --smoke-b: #4a4445;
  }
  * { margin: 0; padding: 0; box-sizing: border-box; }
  html, body { width: 1200px; height: 1015px; overflow: hidden; }
  body {
    background: var(--backdrop);
    display: flex;
    flex-direction: column;
    align-items: center;
    justify-content: center;
    gap: 60px;
  }
  .card {
    width: 700px;
    height: 400px;
    background: var(--card);
    position: relative;
    box-shadow: 0 10px 30px rgba(0,0,0,.25);
  }
  .card--front {
    display: flex;
    flex-direction: column;
    align-items: center;
    justify-content: center;
  }
  .brand-name {
    font-family: "Montserrat", sans-serif;
    font-weight: 700;
    font-size: 44px;
    letter-spacing: 2px;
    color: var(--ink);
    text-transform: uppercase;
  }
  .brand-rule {
    width: 440px;
    height: 1px;
    background: var(--rule);
    margin: 18px 0 40px;
  }
  .tagline {
    font-family: "Montserrat", sans-serif;
    font-weight: 600;
    font-size: 20px;
    letter-spacing: 3px;
    color: var(--ink);
    text-transform: uppercase;
  }
  .smoke-art {
    position: absolute;
    left: 50px;
    top: 30px;
    width: 620px;
    height: 150px;
    background: linear-gradient(100deg, transparent 0%, var(--smoke-a) 35%, var(--smoke-b) 75%, var(--smoke-a) 100%);
    border-radius: 120px 10px 10px 140px;
    opacity: .85;
  }
  .contact {
    position: absolute;
    left: 64px;
    top: 206px;
    font-family: "Arimo", sans-serif;
    color: var(--ink);
  }
  .contact__name {
    font-weight: 700;
    font-size: 26px;
    line-height: 30px;
    text-transform: uppercase;
    letter-spacing: .5px;
  }
  .contact__role {
    font-size: 19px;
    line-height: 22px;
    color: var(--ink-soft);
    margin-bottom: 30px;
  }
  .contact__list { list-style: none; }
  .contact__item {
    display: flex;
    align-items: center;
    gap: 10px;
    font-size: 20px;
    line-height: 27px;
  }
  .contact__item svg { width: 16px; height: 16px; flex: none; }
</style>
</head>
<body>
  <section class="card card--front">
    <div class="brand-name">Calden Leafworks</div>
    <div class="brand-rule"></div>
    <div class="tagline">Savor every leaf</div>
  </section>

  <section class="card card--back">
    <div class="smoke-art" role="img" aria-label="Illustration of a cigar with curling smoke drifting to the left"></div>
    <div class="contact">
      <div class="contact__name">Kevin Oldacre</div>
      <div class="contact__role">Owner</div>
      <ul class="contact__list">
        <li class="contact__item">
          <svg viewBox="0 0 16 16" aria-hidden="true"><circle cx="8" cy="8" r="7" fill="none" stroke="#fff" stroke-width="1.5"/><path d="M5 4.5l1.5-.5 1 2-1 .8a5 5 0 0 0 2.7 2.7l.8-1 2 1-.5 1.5c-3 .3-6.8-3.5-6.5-6.5z" fill="#fff"/></svg>
          555-017-4863
        </li>
        <li class="contact__item">
          <svg viewBox="0 0 16 16" aria-hidden="true"><rect x="1" y="3" width="14" height="10" fill="#fff"/><path d="M1 3l7 6 7-6" fill="none" stroke="#2b2728" stroke-width="1.3"/></svg>
          koldacre@caldenleaf.com
        </li>
        <li class="contact__item">
          <svg viewBox="0 0 16 16" aria-hidden="true"><circle cx="8" cy="8" r="7" fill="#fff"/><path d="M1 8h14M8 1v14M3 4.5h10M3 11.5h10" stroke="#2b2728" stroke-width="1"/><ellipse cx="8" cy="8" rx="3" ry="7" fill="none" stroke="#2b2728" stroke-width="1"/></svg>
          caldenleafworks.com
        </li>
      </ul>
    </div>
  </section>
</body>
</html>
```